Brightway Haul & Upkeep Services, are a company that offers a 'one stop shop' pre-move clean up a

I have already selected a logo which I would like on the front of the business cards along with phone numbers, web address and email which are:
0487650392
www.brightwayhaul.com.au
brightwayhaulandupkeep@mailbox.example

On the back of the card I would like to list some of the types of service we offer (clean - move - repairs/maintenance) which are:
CLEAN - windows, gutters, solar panels, driveways/paths, carpets.
MOVE - Small/medium size house/office moves, large item pick-up & delivery, yard clean-up and removal.
General maintenance and repairs.

I would like the blue logo on a gray background.

Thanks

```html
<!DOCTYPE html>
<html lang="en">
<head>
<meta charset="utf-8">
<title>Brightway Haul &amp; Upkeep Services – Business Card</title>
<link rel="stylesheet" href="https://fonts.googleapis.com/css2?family=Ubuntu:wght@300;400;700&display=swap">
<style>
  :root {
    --brand-blue: #1565ad;
    --card-grey: #d8d9da;
    --card-white: #ffffff;
    --stage: #3a3a3a;
    --ink-dark: #222222;
    --truck-tone: #eef0f2;
  }
  * { margin: 0; padding: 0; box-sizing: border-box; }
  html, body {
    width: 1200px; height: 900px; overflow: hidden;
    background: var(--stage);
    font-family: "Ubuntu", sans-serif;
  }
  .stage { position: relative; width: 1200px; height: 900px; }

  .card {
    position: absolute; top: 295px;
    width: 560px; height: 310px;
    border-radius: 18px; overflow: hidden;
  }
  .card--front { left: 30px; background: var(--card-grey); }
  .card--back  { left: 610px; background: var(--card-white); }

  .card__band {
    position: absolute; left: 0; right: 0; bottom: 0; height: 112px;
    background: var(--brand-blue);
  }

  /* Front */
  .brand-name {
    position: absolute; right: 32px; top: 70px;
    text-align: right; color: var(--brand-blue);
    font-weight: 700; text-transform: uppercase; line-height: 1.08;
  }
  .brand-name__main { display: block; font-size: 40px; }
  .brand-name__sub { display: block; font-size: 21px; }

  .contact {
    position: absolute; right: 30px; bottom: 20px;
    list-style: none; text-align: right;
    color: var(--card-white); font-weight: 300; font-size: 15px; line-height: 21px;
  }
  .contact li { display: flex; justify-content: flex-end; align-items: center; gap: 5px; }
  .contact svg { width: 12px; height: 12px; flex: none; }

  /* Back */
  .abn {
    position: absolute; right: 30px; top: 28px;
    font-family: "Arial", sans-serif; font-size: 12px; color: var(--ink-dark);
  }
  .services {
    position: absolute; left: 30px; top: 30px; width: 330px;
    color: var(--brand-blue); font-weight: 400; font-size: 16px; line-height: 21px;
  }
  .services p { margin-bottom: 9px; }

  .back-brand {
    position: absolute; left: 32px; bottom: 36px;
    color: var(--card-white); font-weight: 700; text-transform: uppercase;
    font-size: 16px; line-height: 1.1;
  }
  .back-brand small { display: block; font-size: 10px; }

  .truck-art {
    position: absolute; right: 32px; bottom: 22px;
    width: 112px; height: 64px; border-radius: 6px;
    background: linear-gradient(180deg, var(--card-white), var(--truck-tone));
  }
</style>
</head>
<body>
<main class="stage">

  <section class="card card--front" aria-label="Card front">
    <h1 class="brand-name">
      <span class="brand-name__main">Brightway Haul</span>
      <span class="brand-name__sub">&amp; Upkeep Services</span>
    </h1>
    <div class="card__band"></div>
    <ul class="contact">
      <li>0487 650 392
        <svg viewBox="0 0 12 12" aria-hidden="true"><path d="M3 1l2 2.5-1.2 1.2a6 6 0 0 0 3.5 3.5L8.5 7 11 9l-1.2 1.8C5.5 10.5 1.5 6.5 1.2 2.2z" fill="none" stroke="currentColor" stroke-width="0.9"/></svg>
      </li>
      <li>www.brightwayhaul.com.au
        <svg viewBox="0 0 12 12" aria-hidden="true"><circle cx="6" cy="6" r="5" fill="none" stroke="currentColor" stroke-width="0.9"/><ellipse cx="6" cy="6" rx="2.2" ry="5" fill="none" stroke="currentColor" stroke-width="0.8"/><path d="M1 6h10" stroke="currentColor" stroke-width="0.8"/></svg>
      </li>
      <li>brightwayhaulandupkeep@mailbox.example
        <svg viewBox="0 0 12 12" aria-hidden="true"><rect x="1" y="2.5" width="10" height="7" fill="currentColor"/><path d="M1 2.5l5 4 5-4" fill="none" stroke="var(--brand-blue)" stroke-width="0.9"/></svg>
      </li>
    </ul>
  </section>

  <section class="card card--back" aria-label="Card back">
    <div class="abn">ABN 48915302774</div>
    <div class="services">
      <p>CLEAN - windows, gutters, solar panels, driveways/paths, carpets.</p>
      <p>MOVE - Small/medium size house/office moves, large item pick-up &amp; delivery, yard clean-up and removal.</p>
      <p>General maintenance and repairs.</p>
    </div>
    <div class="card__band"></div>
    <div class="back-brand">Brightway Haul<small>&amp; Upkeep Services</small></div>
    <div class="truck-art" role="img" aria-label="Illustration of a white removal truck"></div>
  </section>

</main>
</body>
</html>
```